Design a New Business Card for Our Company

We are looking for fresh, unique, and a modern business card that reflects our roots as digital marketing agency focused on SEM.

Industry/Entity Type

Marketing

Contact Information for Business Card

looking for very unique out of the box designs. clean and modern that compliments our logo

Requirements
Must have
• colors should match our logo
• Front should have name, address, email, and phone/fax of the person, phone/fax are the same number
• back should have our url

```html
<!DOCTYPE html>
<html lang="en">
<head>
<meta charset="utf-8">
<title>Brightway Partners Business Card</title>
<link href="https://fonts.googleapis.com/css2?family=Roboto:wght@400;500;700&display=swap" rel="stylesheet">
<style>
  :root {
    --backdrop: #b3b2b2;
    --card: #ffffff;
    --brand-blue: #4a8fd4;
    --text-grey: #6f6f6f;
    --soft-grey: #a9a9a9;
    --decor-grey: #ececec;
  }
  * { margin: 0; padding: 0; box-sizing: border-box; }
  html, body {
    width: 1200px; height: 1000px; overflow: hidden;
    background: var(--backdrop);
    font-family: "Roboto", Arial, sans-serif;
  }
  .card { position: absolute; background: var(--card); }
  .card-back { left: 314px; top: 22px; width: 571px; height: 349px; }
  .card-front { left: 422px; top: 405px; width: 350px; height: 571px; }

  .pattern-band {
    position: absolute; left: 8px; right: 8px;
    background: linear-gradient(180deg, #f6f6f6, #efefef);
  }
  .pattern-top { top: 6px; height: 120px; }
  .pattern-bottom { top: 232px; height: 110px; }

  .brand {
    position: absolute; display: flex; align-items: center; gap: 12px;
    color: var(--brand-blue); font-weight: 500; letter-spacing: -0.5px;
  }
  .brand-dot { border-radius: 50%; background: var(--brand-blue); flex: none; }
  .card-back .brand { left: 0; right: 0; top: 148px; justify-content: center; font-size: 44px; }
  .card-back .brand-dot { width: 34px; height: 34px; }
  .card-front .brand { left: 0; right: 0; top: 70px; justify-content: center; font-size: 32px; }
  .card-front .brand-dot { width: 26px; height: 26px; }

  .website {
    position: absolute; left: 0; right: 0; top: 310px; text-align: center;
    color: var(--brand-blue); font-weight: 500; font-size: 17px;
  }

  .name-row { position: absolute; left: 8px; right: 8px; top: 196px; text-align: center; }
  .name-row::before, .name-row::after {
    content: ""; position: absolute; top: 13px; height: 2px; width: 117px; background: var(--brand-blue);
  }
  .name-row::before { left: 0; }
  .name-row::after { right: 0; }
  .person-name { color: var(--brand-blue); font-weight: 700; font-size: 20px; line-height: 26px; }
  .person-title { color: var(--soft-grey); font-size: 16px; line-height: 18px; }

  .decor-area {
    position: absolute; left: 38px; top: 228px; width: 266px; height: 343px;
    border-radius: 50% 50% 40% 40%;
    background: radial-gradient(circle at 50% 50%, #f3f3f3 0%, var(--decor-grey) 70%, rgba(236,236,236,0) 100%);
  }

  .contact { position: absolute; left: 0; right: 0; text-align: center; color: var(--text-grey); font-size: 14.5px; line-height: 19px; }
  .contact svg { display: block; margin: 0 auto 3px; }
  .contact-address { top: 258px; }
  .contact-phone { top: 367px; }
  .contact-fax { top: 424px; }
  .contact-email { top: 496px; }
</style>
</head>
<body>

<section class="card card-back">
  <div class="pattern-band pattern-top" role="img" aria-label="Faint repeating brand pattern"></div>
  <div class="brand"><span class="brand-dot"></span>brightway partners</div>
  <div class="pattern-band pattern-bottom" role="img" aria-label="Faint repeating brand pattern"></div>
  <p class="website">www.brightwaypartners.com</p>
</section>

<section class="card card-front">
  <div class="brand"><span class="brand-dot"></span>brightway partners</div>

  <div class="decor-area" role="img" aria-label="Large soft brand decoration behind contact details"></div>

  <div class="name-row">
    <p class="person-name">Alan Reyes</p>
    <p class="person-title">President</p>
  </div>

  <div class="contact contact-address">
    <svg width="26" height="26" viewBox="0 0 26 26" fill="none" stroke="#4a8fd4" stroke-width="1.6">
      <circle cx="13" cy="13" r="12"/>
      <path d="M13 20c-3-4-4.5-6-4.5-8a4.5 4.5 0 0 1 9 0c0 2-1.5 4-4.5 8z"/>
      <circle cx="13" cy="11.8" r="1.5"/>
    </svg>
    4580 Maple Ridge Rd<br>Fairview Hills,<br>OR 97301 USA
  </div>

  <div class="contact contact-phone">
    <svg width="26" height="26" viewBox="0 0 26 26" fill="none" stroke="#4a8fd4" stroke-width="1.6">
      <circle cx="13" cy="13" r="12"/>
      <path d="M9 7.5l2 3-1.3 1.5c.8 1.8 2.2 3.2 4 4l1.5-1.3 3 2-1.2 2c-4.5 0-9.5-5-9.5-9.5z" fill="#4a8fd4"/>
    </svg>
    555-014-2290
  </div>

  <div class="contact contact-fax">
    <svg width="26" height="26" viewBox="0 0 26 26" fill="none" stroke="#4a8fd4" stroke-width="1.6">
      <circle cx="13" cy="13" r="12"/>
      <rect x="8.5" y="6.5" width="9" height="5" fill="#fff"/>
      <rect x="6.5" y="11" width="13" height="6" rx="1" fill="#4a8fd4"/>
      <rect x="9" y="15" width="8" height="4.5" fill="#fff"/>
    </svg>
    555-014-2290
  </div>

  <div class="contact contact-email">
    <svg width="26" height="26" viewBox="0 0 26 26" fill="none" stroke="#4a8fd4" stroke-width="1.6">
      <circle cx="13" cy="13" r="12"/>
      <rect x="6.5" y="8.5" width="13" height="9" fill="#4a8fd4"/>
      <path d="M6.5 8.5l6.5 5 6.5-5" stroke="#fff"/>
    </svg>
    hello@brightway.com
  </div>
</section>

</body>
</html>
```